Vortaleen - Lead the Way!

Vortaleen is a new Silicon Valley company, of the pimrela founders from Berlin, which provides a "Shared Hive Circle". This platform allows the crowd to support startups with money, experts and fame. Our Vision is, that everyone should become an entrepreneur.

Pls find all brief details in the attached document
Updates

Would be nice to have a list of more social services I'm available on, like a list of pictograms of all my services:

Find me on: chattro, fennwix+, qrt, mivrel, datebloom, pohk, rplex, etc...

pls make sure to use the right font:
http://www.typelarder-demo.com/fonts/Orbitron

Target Market(s)

Main target market is those already involved in the startup industry, by fundraising, investing, advising, cofounding and working. Vortaleen brings a totaly new transparency and collaborative way of starting companies to that business.

· Entrepreneurs (looking for funding, team and community)
· Investors (looking for hot investments and )
· Experts (workers looking for startups they can work for equity)
· Incubators & Business Schools (looking for tools to advise startups)

Industry/Entity Type

It Company

Requirements
Must have
• Pls find all brief details in the attached document
Nice to have

```html
<!DOCTYPE html>
<html lang="en">
<head>
<meta charset="utf-8">
<title>Vortaleen – Business Card</title>
<link rel="stylesheet" href="https://fonts.googleapis.com/css2?family=Orbitron:wght@500;700&family=Arimo:wght@400;700&display=swap">
<style>
  :root {
    --backdrop: #e9e4df;
    --space-deep: #05070f;
    --space-mid: #101a3e;
    --space-glow: #1f3478;
    --accent: #f0693a;
    --text-light: #ffffff;
    --rule: rgba(255,255,255,0.35);
    --moon-light: #b9b7b2;
    --moon-dark: #56544f;
  }
  * { margin: 0; padding: 0; box-sizing: border-box; }
  html, body { width: 1200px; height: 900px; overflow: hidden; }
  body { background: var(--backdrop); position: relative; }

  .card {
    position: absolute; top: 176px; width: 314px; height: 548px;
    border-radius: 20px; overflow: hidden; color: var(--text-light);
    box-shadow: 0 6px 18px rgba(0,0,0,0.25);
  }

  /* Front */
  .card-front {
    left: 271px;
    font-family: "Arimo", Arial, sans-serif;
    background:
      radial-gradient(ellipse 70% 32% at 62% 16%, var(--space-glow) 0%, rgba(31,52,120,0) 100%),
      linear-gradient(180deg, var(--space-mid) 0%, #0a1128 40%, var(--space-deep) 62%, var(--space-deep) 100%);
  }
  .brand-mark {
    position: absolute; left: 131px; top: 48px; width: 52px; height: 52px;
    border-radius: 50%; background: var(--accent);
  }
  .brand-name {
    position: absolute; left: 48px; top: 136px;
    font-size: 34px; font-weight: 700; letter-spacing: 0.5px;
  }
  .brand-tagline {
    position: absolute; right: 28px; top: 186px;
    font-size: 15px; font-weight: 700;
  }
  .holder { position: absolute; left: 40px; top: 348px; }
  .holder-name { font-size: 18px; font-weight: 700; }
  .holder-role { font-size: 15px; margin-top: 2px; }
  .contact-list {
    position: absolute; left: 40px; top: 402px; list-style: none;
  }
  .contact-list li {
    display: flex; align-items: center; gap: 10px;
    font-size: 18px; height: 22px; line-height: 22px;
  }
  .contact-list svg { width: 14px; height: 14px; flex: none; }

  /* Back */
  .card-back {
    left: 614px; text-align: center;
    font-family: "Orbitron", sans-serif; font-weight: 500;
    background:
      radial-gradient(ellipse 60% 22% at 72% 2%, #3a5cb4 0%, rgba(58,92,180,0) 100%),
      linear-gradient(180deg, var(--space-glow) 0%, var(--space-mid) 30%, #090e22 60%, var(--space-deep) 100%);
  }
  .headline-top { position: absolute; left: 0; right: 0; top: 38px; font-size: 38px; }
  .headline-sub { position: absolute; left: 0; right: 0; top: 90px; font-size: 23px; }
  .interests { position: absolute; left: 30px; right: 30px; top: 144px; list-style: none; }
  .interests li {
    font-size: 16px; line-height: 23px; padding: 10px 0 14px;
    border-bottom: 1px solid var(--rule);
  }
  .interests li:last-child { border-bottom: none; }
  .social-line {
    position: absolute; left: 0; right: 0; top: 380px;
    display: flex; justify-content: center; align-items: center; gap: 8px;
    font-size: 10px;
  }
  .network-name { font-size: 14px; font-weight: 700; }
  .web-address {
    position: absolute; left: 0; right: 0; top: 424px;
    font-size: 10px; letter-spacing: 3px;
  }
  .moon-surface {
    position: absolute; left: -60px; right: -60px; top: 468px; height: 260px;
    border-radius: 50%;
    background: radial-gradient(ellipse 60% 40% at 50% 20%, var(--moon-light) 0%, #8d8b86 50%, var(--moon-dark) 100%);
    box-shadow: 0 -6px 18px rgba(200,210,230,0.35);
  }
</style>
</head>
<body>

<section class="card card-front">
  <div class="brand-mark"></div>
  <div class="brand-name">Vortaleen</div>
  <div class="brand-tagline">Lead the Way!</div>

  <div class="holder">
    <div class="holder-name">Lukas Renner</div>
    <div class="holder-role">Founder and CEO</div>
  </div>

  <ul class="contact-list">
    <li>
      <svg viewBox="0 0 14 14"><rect x="3" y="0" width="8" height="14" rx="1.5" fill="#f0693a"/><rect x="4.5" y="2" width="5" height="6" fill="#05070f"/></svg>
      0400 3117
    </li>
    <li>
      <svg viewBox="0 0 14 14"><rect x="0.5" y="2.5" width="13" height="9" fill="none" stroke="#f0693a" stroke-width="1.3"/><path d="M0.5 2.5 L7 8 L13.5 2.5" fill="none" stroke="#f0693a" stroke-width="1.3"/></svg>
      lukas@vortaleen.com
    </li>
    <li>
      <svg viewBox="0 0 14 14"><rect x="1" y="1" width="12" height="12" rx="1.5" fill="#f0693a"/></svg>
      /lukasrenner
    </li>
    <li>
      <svg viewBox="0 0 14 14"><rect x="1" y="1" width="12" height="12" rx="1.5" fill="#f0693a"/></svg>
      /lukasrenner
    </li>
    <li>
      <svg viewBox="0 0 14 14"><rect x="1" y="1" width="12" height="12" rx="1.5" fill="#f0693a"/></svg>
      /in/lukasrenner
    </li>
  </ul>
</section>

<section class="card card-back">
  <div class="headline-top">Are you</div>
  <div class="headline-sub">interested in?</div>

  <ul class="interests">
    <li>Starting your own<br>Business?</li>
    <li>Investing in hot<br>Startups?</li>
    <li>Working for the<br>next “Friendora”?</li>
  </ul>

  <div class="social-line">
    <span>Join us on</span>
    <span class="network-name">Friendora</span>
    <span>/Vortaleen</span>
  </div>

  <div class="web-address">www.vortaleen.com</div>

  <div class="moon-surface" role="img" aria-label="Photograph of the lunar surface curving across the bottom of the card"></div>
</section>

</body>
</html>
```